Nutritional & Gastrointestinal Health Consulting Service-Website design

We need a website design for a new health consulting service called "Bright Vale" based in Perth, Australia.

We will be providing consulting services in the areas of:
1) Nutrition and Diet
2) Gastrointestinal Health (which means stomach & digestive system related health)

These consulting services will be provided by an Accredited Dietitian and a Paediatric Gastroenterologist.

We are open to creative ideas in terms of design, layout, fonts and colours. We also would love to see images of nature in the backdrop with families (adults with kids) having a good time, fresh fruits and vegetables displayed in a farmer's market or supermarket. 2 or 3 images should be sufficient. We would also definitely want our logo somewhere in the main page of website. The logo file is also attached. Please have a look at a website's design that we really liked. We would love to see designs inspired by that style. The website details are in the in the "nice to have priorities" section of this project brief.

We also would be looking at website designers with software coding skills so that if we like the design we can go ahead with the next step of coding.

The website design should communicate the purpose of the website and at the same time be simple, elegant and unique/eye-catching.

We look forward to receiving creative ideas for our website from you all. Good luck!

More details have been added to our project- for example: Logo, fonts style, must haves etc etc. Please view the updated project brief. Looking forward to receiving your fantastic ideas for our website. Thanking you

Hi, I have updated the colour preference. Will add the content preferences tomorrow. thanks

Hello all, I have now added a LOT more content to what we want in our website. It is very much in detail, so please carefully have a read through the entire project brief. If you have any questions write back to me and I will try to respond as quickly as I can. Last few days were busy so couldn't respond quickly to all of you who had send me designs/queries/questions. Thank you for your patience. I look forward to receiving fantastic designs from you all. Good Luck :-)

Target Market(s)

Adults based in western speaking countries aged 18 to 60 years

Industry/Entity Type

Software

Font styles to use
Sans Serif
Script

Colors
faa54b
acd036

Requirements
Must have
• The website must have the MAIN logo file attached. I have attached 3 files: 1) MAIN logo; 2) supplementary logo A ; 3) supplementary logo B

I have selected 2 colours from the colour scheme (see below)-(as the colour of our logo is that).
However we would also like to see LIGHT CHOCOLATE BROWN or CHOCOLATE BROWN colour used as the background colour of the website
Preferred WEBSITE CONTENT:
1) HOME PAGE:
Content required=
--Company Logo
--Dr Dorian Pelham
Paediatric Gastroenterologist & Hepatologist
-Marla Pelham.
Dietitian & Nutritionist
--Website Menu (either listed horizontally or vertically):
Once clicked on each name:

Under each of the Website Menu items we want the following Headings to be added

2) ABOUT US page:
Sub-heading under this: Qualification, Skills, Special Interest

3) SERVICES
DORIAN'S PAGE: Individual Consultation, Endoscopy procedures
Individual Consultation, Group Based Services, Food Diary, Food & Symptom Diary

4) FEES & REBATE: Content as below:
Please Note: Payment of full fees is required at the time of consultation and procedures. 48 hours notice is required for cancellation of appointments/non-attendance. Failure to provide this may result in a fee being incurred. Please call reception to find out the amount of fee charged for cancellation of appointments/non-attendance.
headings are:
Paediatric Gastroenterology:
Dorian's pge
Individual Consultation - Initial (upto 30 mins):
Review Consultation (upto 15 mins):
Endoscopy procedures - No Gap fees charged. Fees will be billed directly to Vitacover. If any queries, please contact reception.

marla's pge
sub heading:
Individual Consultation - Initial (upto 45 mins):
Individual Consultation - Review (upto 30 mins):

Concession-Individual Consultation -Initial (upto 45 mins):
Concession-Individual Consultation - Review (upto 30 mins):
Please Note: Concession applies for health care card holders & pensioners

Group Based Services: Pricing subject to the type of service provided. Please contact us for an obligation free quote.
Education Topics Include:
- Paediatric Nutrition (Introducing Solids, Fussy Eating, Healthy Eating)
- Pregnancy Nutrition, Gestational Diabetes, Breastfeeding/Lactation Nutrition
- Healthy Eating, Supermarket Shopping Tips, Nutrition Label Reading Tips, Healthier
sub heading under nutrition & diet:
-Vitacover:
--A rebate of $52.95 is available from Vitacover if an EPC ( Enhanced Primary Care)/Chronic Disease Management (CDM) plan is issued by your GP.
--All mandatory paperwork needs to be available at the time of making your appointment for your eligibility.
-Private Health Fund:
--Most private health funds provide rebate on dietetic appointments. However the rebate amount depends on your level of cover. Thus, please contact your health fund to determine your entitled rebate.
-RSB: Approved provider for RSB services

6) FOR DOCTORS: Bright Vale Paediatric Gastroenterologist Referral Form
Bright Vale Dietitian Referral form
7) LOCATIONS & CONTACT

Paediatric Gastroenterology & Hepatology Service
Suite 46
Holy Lantern Bramcote Medical Centre
17 Colin Ferris Pde,
MURDOCH, WA 6150
P: (08) 9422 5061
F: (08) 9422 3094

Nutrition & Diet Service
Suite 46
17 Colin Ferris Pde,
MURDOCH, WA 6150
P: (08) 9422 5061
F: (08) 9422 3094

Tolland Medical Centre
58-60 Karrigan Parkway,
MANDURAH, WA 6210
P: (08) 9647 2283
F: (08) 96724419
www.tmcexample.com.au

This page should have a webform that has following titles:
-Your Name
-Your Email
-Your Phone
-Message

8) NEWS & BLOG
Nice to have
• We liked the design style of the websites below:
https://www.vendoraplex.example/

http://qoravelt.example/

But feel free to use your creativity too
Should not have
• Please do not use any body building or muscle building images

```html
<!DOCTYPE html>
<html lang="en">
<head>
<meta charset="utf-8">
<title>Bright Vale — Paediatric Gastroenterology</title>
<link href="https://fonts.googleapis.com/css2?family=Open+Sans:wght@300;400;600;700&family=Raleway:wght@500;600;800;900&display=swap" rel="stylesheet">
<style>
:root{
  --brown:#4a2c28;
  --brown-deep:#3f2521;
  --orange:#faa54b;
  --green:#acd036;
  --green-text:#9cc03a;
  --red:#d4322b;
  --white:#ffffff;
  --ink:#3a2a26;
}
*{margin:0;padding:0;box-sizing:border-box}
html,body{width:1144px;height:1200px;overflow:hidden;background:var(--brown)}
body{position:relative;font-family:"Open Sans",sans-serif;color:var(--ink)}
.abs{position:absolute}

/* header */
.site-header{left:0;top:0;width:1144px;height:86px;background:var(--brown)}
.brand{left:63px;top:24px;display:flex;align-items:center;gap:10px}
.brand-dot{width:34px;height:34px;border-radius:50%;background:var(--orange)}
.brand-name{font-family:"Raleway",sans-serif;font-weight:800;font-size:26px;color:var(--green);letter-spacing:.5px}
.main-nav{left:291px;top:0;height:86px;display:flex}
.nav-item{height:86px;display:flex;flex-direction:column;align-items:center;justify-content:center;gap:7px;padding:0 15px;border-right:1px solid #3c2320;color:var(--white);font-weight:700;font-size:11.5px;letter-spacing:.2px;white-space:nowrap}
.nav-item svg{width:11px;height:11px}
.nav-item.is-active{background:var(--orange);width:63px;padding:0}
.header-rule{left:0;top:86px;width:1120px;height:3px;background:var(--red)}
.header-rule-end{left:1120px;top:86px;width:24px;height:3px;background:#1d2430}

/* hero */
.hero{left:0;top:89px;width:1144px;height:449px;background:linear-gradient(90deg,#fbfbf8 0%,#f6f6f1 40%,#b7b8a8 55%,#8a8c7a 68%,#b9c6d2 85%,#dfe3da 100%)}
.hero-kicker{left:134px;top:185px;font-family:"Raleway",sans-serif;font-weight:800;font-size:27px;color:var(--green);letter-spacing:-.3px}
.hero-title{left:131px;top:210px;font-family:"Raleway",sans-serif;font-weight:900;font-size:70px;color:var(--orange);letter-spacing:-1px;line-height:1}
.hero-rule{left:134px;top:289px;width:768px;height:3px;background:#f6d9b2}
.hero-copy{left:134px;top:311px;width:420px;font-size:13.5px;line-height:21.5px;color:#333}
.hero-button{left:134px;top:385px;width:113px;height:38px;background:var(--green);color:var(--brown);font-weight:700;font-size:12px;letter-spacing:1.2px;display:flex;align-items:center;justify-content:center}

/* services */
.services{left:0;top:540px;width:1144px;height:332px;background:var(--brown)}
.service{top:0;width:330px;text-align:center}
.service-icon{position:absolute;left:50%;top:65px;transform:translateX(-50%)}
.service-title{position:absolute;left:0;top:170px;width:100%;font-family:"Raleway",sans-serif;font-weight:500;font-size:17.5px;color:var(--orange)}
.service-sub{position:absolute;left:0;top:196px;width:100%;font-size:11px;letter-spacing:1px;color:var(--green-text)}
.service-divider{position:absolute;left:50%;top:227px;width:28px;height:1px;margin-left:-14px;background:#b98a6a}
.service-link{position:absolute;left:0;top:249px;width:100%;font-size:12.5px;color:var(--green);display:flex;justify-content:center;align-items:center;gap:4px}
.green-rule{left:0;top:872px;width:1144px;height:3px;background:var(--green)}

/* footer */
.site-footer{left:0;top:875px;width:1144px;height:304px;background:var(--orange)}
.footer-brand{left:63px;top:65px;width:151px;display:flex;flex-direction:column;align-items:center;gap:14px}
.footer-dot{width:62px;height:62px;border-radius:50%;background:var(--white)}
.footer-name{font-family:"Raleway",sans-serif;font-weight:800;font-size:26px;color:var(--white)}
.footer-heading{font-family:"Raleway",sans-serif;font-weight:500;font-size:23px;color:var(--white)}
.footer-about{left:240px;top:62px}
.footer-about p{margin-top:27px;width:330px;font-weight:300;font-size:12px;line-height:20px;color:var(--white)}
.footer-col{top:62px}
.footer-col ul{list-style:none;margin-top:24px;padding-left:5px}
.footer-col li{font-weight:300;font-size:12.5px;color:var(--white);height:27px}
.base-bar{left:0;top:1179px;width:1144px;height:21px;background:var(--brown)}
</style>
</head>
<body>

<header class="abs site-header">
  <div class="abs brand"><span class="brand-dot"></span><span class="brand-name">Bright Vale</span></div>
  <nav class="abs main-nav">
    <div class="nav-item is-active"><svg viewBox="0 0 12 12"><path d="M1 6 6 1.5 11 6M2.5 5v5.5h7V5" fill="none" stroke="#fff" stroke-width="1.4" opacity=".7"/></svg>HOME</div>
    <div class="nav-item"><svg viewBox="0 0 12 12"><path d="M1 2h2M5 2h6M1 6h2M5 6h6M1 10h2M5 10h6" stroke="#bfa9a3" stroke-width="1.5"/></svg>ABOUT US</div>
    <div class="nav-item"><svg viewBox="0 0 12 12"><rect x="1" y="2" width="10" height="9" fill="none" stroke="#bfa9a3" stroke-width="1.3"/><path d="M1 5h10" stroke="#bfa9a3"/></svg>NUTRITION &amp; DIET</div>
    <div class="nav-item"><svg viewBox="0 0 12 12"><path d="M6 1v10M3 3h6M4 6h4" stroke="#bfa9a3" stroke-width="1.3"/></svg>PAEDIATRIC GASTROENTEROLOGY</div>
    <div class="nav-item"><svg viewBox="0 0 12 12"><path d="M1 3h4l1 1.5h5V10H1z" fill="none" stroke="#bfa9a3" stroke-width="1.2"/></svg>FEES &amp; REBATE</div>
    <div class="nav-item"><svg viewBox="0 0 12 12"><path d="M3 1v4a3 3 0 0 0 6 0V1M6 8v2a2 2 0 0 0 4 0" fill="none" stroke="#bfa9a3" stroke-width="1.2"/></svg>DOCTORS</div>
    <div class="nav-item" style="border-right:0"><svg viewBox="0 0 12 12"><rect x="1" y="2.5" width="10" height="7" fill="#bfa9a3"/><path d="M1 2.5 6 6.5 11 2.5" fill="none" stroke="#4a2c28"/></svg>CONTACTS</div>
  </nav>
</header>
<div class="abs header-rule"></div>
<div class="abs header-rule-end"></div>

<section class="abs hero" role="img" aria-label="Photo of a smiling family walking outdoors in nature, parents swinging a young child between them"></section>
<div class="abs hero-kicker">COMPREHENSIVE PAEDIATRIC</div>
<h1 class="abs hero-title">GASTROENTEROLOGY</h1>
<div class="abs hero-rule"></div>
<p class="abs hero-copy">Bright Vale team includes a Paediatric Gastroenterologist - Dr Dorian Pelham and an Accredited Dietitian-Marla Pelham. Welcome to a comprehensive paediatric gastroenterology service.</p>
<div class="abs hero-button">READ MORE</div>

<section class="abs services">
  <div class="abs service" style="left:61px">
    <svg class="service-icon" width="60" height="84" viewBox="0 0 60 84" role="img" aria-label="Fresh fruit illustration"><circle cx="30" cy="48" r="28" fill="var(--orange)"/></svg>
    <div class="service-title">Nutrition and Diet</div>
    <div class="service-sub">INDIVIDUAL CONSULTATION</div>
    <div class="service-divider"></div>
    <div class="service-link">read more <svg width="11" height="11" viewBox="0 0 12 12"><circle cx="6" cy="6" r="6" fill="var(--green)"/><path d="M4.5 3 7.5 6 4.5 9" fill="none" stroke="#4a2c28" stroke-width="1.6"/></svg></div>
  </div>
  <div class="abs service" style="left:414px">
    <svg class="service-icon" width="60" height="84" viewBox="0 0 60 84" role="img" aria-label="Digestive system illustration"><circle cx="30" cy="48" r="28" fill="var(--orange)"/></svg>
    <div class="service-title">Gastrointestinal Health</div>
    <div class="service-sub">GASTROINTESTINAL AND LIVER DISORDERS</div>
    <div class="service-divider"></div>
    <div class="service-link">read more <svg width="11" height="11" viewBox="0 0 12 12"><circle cx="6" cy="6" r="6" fill="var(--green)"/><path d="M4.5 3 7.5 6 4.5 9" fill="none" stroke="#4a2c28" stroke-width="1.6"/></svg></div>
  </div>
  <div class="abs service" style="left:767px">
    <svg class="service-icon" width="50" height="78" viewBox="0 0 50 78"><path d="M25 4a19 19 0 0 0-19 19c0 14 19 36 19 36s19-22 19-36A19 19 0 0 0 25 4z" fill="var(--orange)"/><circle cx="25" cy="23" r="7" fill="var(--brown)"/><ellipse cx="25" cy="66" rx="20" ry="7" fill="none" stroke="var(--orange)" stroke-width="4"/></svg>
    <div class="service-title">Locations &amp; Contact</div>
    <div class="service-sub">PAEDIATRIC GASTROENTEROLOGY SERVICE</div>
    <div class="service-divider"></div>
    <div class="service-link">read more <svg width="11" height="11" viewBox="0 0 12 12"><circle cx="6" cy="6" r="6" fill="var(--green)"/><path d="M4.5 3 7.5 6 4.5 9" fill="none" stroke="#4a2c28" stroke-width="1.6"/></svg></div>
  </div>
</section>
<div class="abs green-rule"></div>

<footer class="abs site-footer">
  <div class="abs footer-brand"><span class="footer-dot"></span><span class="footer-name">Bright Vale</span></div>
  <div class="abs footer-about">
    <h2 class="footer-heading">About us</h2>
    <p>We would like to see the website design that uses the colour green and yellowish orange (as the colour of our logo is that). We are open to creative ideas in terms of design, layout, fonts and colours. We also would love to see images of nature in the backdrop with families (adults with kids).</p>
  </div>
  <div class="abs footer-col" style="left:593px">
    <h2 class="footer-heading">Site</h2>
    <ul><li>Home</li><li>About us</li><li>Services</li><li>News</li><li>Contact Us</li></ul>
  </div>
  <div class="abs footer-col" style="left:769px">
    <h2 class="footer-heading">Support</h2>
    <ul><li>FAQ's</li><li>Disclaimer</li><li>Support</li><li>Products</li><li>Help</li></ul>
  </div>
  <div class="abs footer-col" style="left:946px">
    <h2 class="footer-heading">Network</h2>
    <ul><li>Friendnote</li><li>Chirpline</li><li>ViewStream</li><li>Snapgrid</li><li>Workmesh</li></ul>
  </div>
</footer>
<div class="abs base-bar"></div>

</body>
</html>
```